KLV Plant Services

We are a heavy diesel mechanical business with additional air con certificates, remapping engine rebuilt

Contact Information for Business Card

Company Name, Director Name, Managing Director, Contact details, email and website

Font styles to use
Serif
Script

```html
<!DOCTYPE html>
<html lang="en">
<head>
<meta charset="utf-8">
<title>KLV Plant Services – Business Card</title>
<link rel="stylesheet" href="https://fonts.googleapis.com/css2?family=Open+Sans:ital,wght@0,400;0,600;0,700;1,400&display=swap">
<style>
  :root {
    --navy: #1c1c7c;
    --navy-line: #2020a0;
    --ink: #14143a;
    --paper: #ffffff;
    --backdrop: #efe7da;
  }
  * { box-sizing: border-box; margin: 0; padding: 0; }
  html, body { width: 1200px; height: 675px; overflow: hidden; }
  body {
    background: var(--backdrop);
    font-family: "Open Sans", sans-serif;
    position: relative;
  }
  .card {
    position: absolute;
    top: 194px;
    width: 500px;
    height: 286px;
    border-radius: 28px;
    box-shadow: 0 10px 24px rgba(60, 40, 20, 0.22);
    overflow: hidden;
  }
  .card-front { left: 70px; background: var(--navy); }
  .card-back  { left: 630px; background: var(--paper); }

  .brand-name {
    position: absolute;
    left: 0; right: 0; top: 124px;
    text-align: center;
    font-size: 30px;
    font-weight: 700;
    color: var(--paper);
    line-height: 1.2;
  }

  .frame { position: absolute; inset: 0; }

  .person {
    position: absolute;
    right: 266px;
    top: 100px;
    text-align: right;
  }
  .person-name {
    font-size: 25px;
    font-weight: 700;
    color: var(--navy);
    line-height: 1.05;
  }
  .person-title {
    font-size: 9.5px;
    font-style: italic;
    color: var(--ink);
    margin-top: 3px;
  }

  .divider {
    position: absolute;
    left: 246px; top: 75px;
    width: 1px; height: 100px;
    background: var(--navy-line);
  }

  .contact-list {
    position: absolute;
    left: 258px; top: 88px;
    list-style: none;
  }
  .contact-item {
    display: flex;
    align-items: center;
    height: 20px;
    font-size: 11.5px;
    font-weight: 600;
    color: var(--ink);
    white-space: nowrap;
  }
  .contact-icon { width: 15px; height: 15px; margin-right: 7px; flex: none; }

  .address {
    position: absolute;
    right: 190px; top: 220px;
    text-align: right;
    font-size: 11.5px;
    font-weight: 600;
    font-style: normal;
    color: var(--ink);
    line-height: 17px;
  }
</style>
</head>
<body>

<section class="card card-front" aria-label="Business card front">
  <p class="brand-name">KLV Plant Services</p>
</section>

<section class="card card-back" aria-label="Business card back">
  <svg class="frame" width="500" height="286" viewBox="0 0 500 286" aria-hidden="true">
    <path d="M90 272 H40 A26 26 0 0 1 14 246 V40 A26 26 0 0 1 40 14 H460 A26 26 0 0 1 486 40 V246 A26 26 0 0 1 460 272 H395"
          fill="none" stroke="var(--navy-line)" stroke-width="2"/>
  </svg>

  <div class="person">
    <p class="person-name">Director Name</p>
    <p class="person-title">Managing Director</p>
  </div>

  <div class="divider"></div>

  <ul class="contact-list">
    <li class="contact-item">
      <svg class="contact-icon" viewBox="0 0 16 16" aria-hidden="true">
        <circle cx="8" cy="8" r="7" fill="none" stroke="var(--navy)" stroke-width="1.2"/>
        <path d="M5.2 5.4c.4-.5 1-.5 1.2 0l.5 1c.1.3 0 .6-.3.8l-.3.2c.4.9 1 1.5 1.9 1.9l.2-.3c.2-.3.5-.4.8-.3l1 .5c.5.2.5.8 0 1.2-.6.6-1.4.7-2.2.3-1.4-.7-2.4-1.7-3.1-3.1-.4-.8-.3-1.6.3-2.2z" fill="var(--navy)"/>
      </svg>
      845 845 8456
    </li>
    <li class="contact-item">
      <svg class="contact-icon" viewBox="0 0 16 16" aria-hidden="true">
        <circle cx="8" cy="8" r="7" fill="none" stroke="var(--navy)" stroke-width="1.2"/>
        <rect x="5.8" y="4" width="4.4" height="8" rx="0.8" fill="none" stroke="var(--navy)" stroke-width="1"/>
      </svg>
      458 458 4569
    </li>
    <li class="contact-item">
      <svg class="contact-icon" viewBox="0 0 16 16" aria-hidden="true">
        <circle cx="8" cy="8" r="7" fill="var(--navy)"/>
        <rect x="4.5" y="5.5" width="7" height="5" fill="#fff"/>
        <path d="M4.5 5.5 L8 8.4 L11.5 5.5" fill="none" stroke="var(--navy)" stroke-width="0.9"/>
      </svg>
      info@websitename.com
    </li>
    <li class="contact-item">
      <svg class="contact-icon" viewBox="0 0 16 16" aria-hidden="true">
        <circle cx="8" cy="8" r="7" fill="none" stroke="var(--navy)" stroke-width="1.2"/>
        <circle cx="8" cy="8" r="4" fill="none" stroke="var(--navy)" stroke-width="1"/>
        <ellipse cx="8" cy="8" rx="1.8" ry="4" fill="none" stroke="var(--navy)" stroke-width="0.9"/>
        <path d="M4 8 H12" stroke="var(--navy)" stroke-width="0.9"/>
      </svg>
      www.websitename.com
    </li>
  </ul>

  <address class="address">
    P.O. Box, Street Name,<br>
    Countryname , ZIPCODE 0000
  </address>
</section>

</body>
</html>
```